Popcorn, ice cream, alcohol infused shakes shop

Create a clean simple website with pictures and bold type for a popcorn, ice cream and boozy shake shop. The site should have:
- Unique and Large Typography
- Large & Responsive Hero (stunning, elicits a response) Images.No concern with above or below the fold. Create a strong visual experience that encourages visitors to scroll down to read more. Use large images to visually tell a story without having to rely on just text.
- Flat image designs
- Place for me to upload an ad type video
- Hidden type menu (three line menu)
- A few small card like images (food, gift bags, tins, etc.) menu items with a brief description.

Target Market(s)

21-49 years of age for the boozy shakes. Soccer moms for sports teams & sleepovers, professionals (teachers, realtors, pharm sales), gifts for family and friends. Also some kids

Coding

Coded - Design and coding required

Number of Pages Required

5+ page

Font styles to use
Sans Serif

Colors

Designer to choose colors to be used in the design.

Requirements
Must have
• Images of gourmet popcorn, fancy shakes, ice cream, gift bags and popcorn tins. Holiday popcorn tins and gift bags along with grift certificates. Ability for visitors to send a contact form to kt@treatloft.example
• Five pages - Home Page, AboutUs, Menu, Gift/Promotion, Contact Us
Nice to have
• Smooth flow on the home page. Mostly images and bold text.
Should not have
• Too many words. Boring text fonts

```html
<!DOCTYPE html>
<html lang="en">
<head>
<meta charset="utf-8">
<title>Treat Loft — Popcorn, Ice Cream &amp; Shakes</title>
<link href="https://fonts.googleapis.com/css2?family=Poppins:wght@400;500;600;700&family=Roboto:wght@300;400;500&display=swap" rel="stylesheet">
<style>
:root{
  --pink:#ec1c5b;
  --pink-deep:#c8134e;
  --wine:#8a0a35;
  --night:#2a0808;
  --ink:#1b1b1b;
  --muted:#555;
  --white:#fff;
}
*{box-sizing:border-box;margin:0;padding:0}
html,body{width:1200px;height:4009px;overflow:hidden;background:var(--white)}
body{font-family:"Roboto",sans-serif;color:var(--ink)}
.page{position:relative;width:1200px;height:4009px;overflow:hidden}
.abs{position:absolute}
.heading{font-family:"Poppins",sans-serif;font-weight:600;letter-spacing:1px}
.accent{color:var(--pink)}
.btn{position:absolute;display:flex;align-items:center;justify-content:center;border:3px solid var(--pink);border-radius:22px;font-size:13px;color:inherit;text-decoration:none}
.photo{position:absolute}

/* hero */
.hero{position:absolute;left:0;top:0;width:1200px;height:674px;background:var(--night);color:var(--white)}
.brand{position:absolute;left:90px;top:40px;font-family:"Poppins",sans-serif;font-weight:700;font-size:22px;color:var(--pink);display:flex;align-items:center;gap:8px}
.brand .dot{width:12px;height:12px;border-radius:50%;background:var(--pink)}
.nav{position:absolute;left:303px;top:47px;display:flex;gap:25px;font-size:13px}
.nav a{color:var(--white);text-decoration:none}
.menu-toggle{position:absolute;left:1112px;top:44px;width:30px;height:22px;display:flex;flex-direction:column;justify-content:space-between}
.menu-toggle span{display:block;height:3px;border-radius:2px;background:var(--white)}
.hero-title{position:absolute;left:92px;top:340px;font-size:50px;line-height:56px}
.hero-sub{position:absolute;left:93px;top:456px;font-size:13.5px;letter-spacing:2.4px}
.hero .btn{left:93px;top:492px;width:153px;height:40px;color:var(--white)}

/* about */
.about-frame{position:absolute;left:93px;top:822px;width:153px;height:438px;border:11px solid var(--pink);border-right:none}
.about-bracket{position:absolute;left:476px;top:859px;width:268px;height:361px;border:15px solid var(--pink);border-right:none}
.about-bracket::before,.about-bracket::after{content:"";position:absolute;right:-1px;width:15px;height:58px;background:var(--pink)}
.about-bracket::before{top:-15px}
.about-bracket::after{bottom:-15px}
.about-title{position:absolute;left:647px;top:938px;font-size:46px}
.about-text{position:absolute;left:647px;top:998px;width:405px;font-size:12px;line-height:25px;color:var(--muted)}
.about .btn{left:646px;top:1085px;width:154px;height:37px}

/* menu */
.menu{position:absolute;left:0;top:1460px;width:1200px;height:830px;background:linear-gradient(180deg,var(--wine) 0%,#a80f40 50%,var(--pink-deep) 100%);color:var(--white)}
.menu-title{position:absolute;left:0;width:1200px;top:90px;text-align:center;font-size:50px}
.tabs{position:absolute;left:60px;top:200px;width:1080px;height:45px;border-bottom:1px solid rgba(255,255,255,.18);font-size:13px}
.tabs span{position:absolute;top:0}
.tabs .active::after{content:"";position:absolute;left:-13px;right:-13px;top:37px;height:5px;background:var(--night)}
.pill{position:absolute;left:560px;top:380px;width:162px;height:62px;background:var(--night);display:flex;align-items:center;justify-content:center;font-size:19px;border-radius:4px}
.menu-text{position:absolute;left:560px;top:462px;width:440px;font-size:12.5px;line-height:25px}
.treat{position:absolute;top:537px;width:110px;text-align:center;font-size:13px}
.treat .ring{width:74px;height:74px;margin:0 auto 12px;border-radius:50%;border:4px solid var(--pink);box-shadow:0 0 0 3px #f4c2cf}
.gift-cards{position:absolute;left:93px;top:640px;width:1014px;display:flex;gap:24px}
.gift-card{flex:1;display:flex;gap:14px;align-items:center;background:rgba(42,8,8,.55);border-radius:8px;padding:12px}
.gift-card .thumb{flex:none;width:76px;height:76px;border-radius:6px}
.gift-card h3{font-family:"Poppins",sans-serif;font-weight:600;font-size:15px;margin-bottom:4px}
.gift-card p{font-size:12px;line-height:18px}

/* gallery */
.gallery{position:absolute;left:0;top:2270px;width:1200px;height:690px;background:linear-gradient(135deg,#3b2a22 0%,#241a16 45%,#4a3b33 100%);color:var(--white)}
.gallery-title{position:absolute;left:577px;top:240px;font-size:50px}
.gallery-text{position:absolute;left:577px;top:310px;width:560px;font-size:12.5px;line-height:30px}
.gallery .btn{left:577px;top:447px;width:153px;height:39px;color:var(--white)}
.video-slot{position:absolute;left:93px;top:2334px;width:420px;height:483px;border-radius:8px;background:radial-gradient(ellipse at 40% 60%,#e9d7d6 0%,#b77766 40%,#3b2a22 78%)}
.play{position:absolute;left:172px;top:204px;width:76px;height:76px;border-radius:50%;background:var(--pink);display:flex;align-items:center;justify-content:center}

/* contact */
.contact-title{position:absolute;left:95px;top:3170px;font-size:52px}
.contact-sub{position:absolute;left:96px;top:3240px;font-size:13px;color:var(--muted)}
.field{position:absolute;border:1.5px solid #555;border-radius:6px;padding:10px 22px;font-size:12.5px;color:#999}
.info h4{position:absolute;left:816px;font-family:"Poppins",sans-serif;font-weight:500;font-size:19px;letter-spacing:.5px}
.info p{position:absolute;left:816px;font-size:12.5px;color:var(--muted);line-height:20px}

/* footer */
.footer{position:absolute;left:0;top:3650px;width:1200px;height:359px;background:var(--pink);color:var(--white)}
.footer .brand{left:101px;top:90px;color:var(--white);font-size:28px}
.footer .brand .dot{background:var(--white)}
.foot-about{position:absolute;left:101px;top:190px;width:345px;font-size:12px;line-height:19.5px}
.foot-col{position:absolute;top:142px}
.foot-col h5{font-family:"Poppins",sans-serif;font-weight:400;font-size:19px;margin-bottom:18px}
.foot-col li{list-style:none;font-size:12px;line-height:19.5px}
.contact-line{display:flex;gap:14px;align-items:flex-start;font-size:12px;line-height:16px;margin-bottom:14px}
.contact-line svg{flex:none}
</style>
</head>
<body>
<div class="page">

  <header class="hero">
    <svg class="abs" style="left:0;top:0" width="1200" height="674" viewBox="0 0 1200 674">
      <defs>
        <linearGradient id="heroScene" x1="0" y1="0" x2="1" y2="1">
          <stop offset="0" stop-color="#5a3a2c"/><stop offset=".5" stop-color="#a98b78"/><stop offset="1" stop-color="#d9c6b8"/>
        </linearGradient>
      </defs>
      <path role="img" aria-label="Restaurant table with plated desserts" d="M900 0 L1200 0 L1200 674 L890 674 C780 520 640 370 470 305 C650 250 800 120 900 0 Z" fill="url(#heroScene)"/>
      <path d="M890 674 C780 520 640 370 470 305" fill="none" stroke="var(--pink)" stroke-width="14"/>
      <path d="M0 225 C300 200 620 260 900 0" fill="none" stroke="var(--pink)" stroke-width="13"/>
      <g stroke="#f0d4dc" stroke-width="10" fill="none">
        <circle cx="724" cy="296" r="125"/><circle cx="990" cy="163" r="82"/><circle cx="965" cy="475" r="106"/><circle cx="1183" cy="296" r="56"/>
      </g>
      <circle role="img" aria-label="Ice cream scoop with caramel popcorn" cx="724" cy="296" r="118" fill="#cdbfae" stroke="var(--pink)" stroke-width="4"/>
      <circle role="img" aria-label="Colourful gourmet popcorn" cx="990" cy="163" r="76" fill="#d9652f" stroke="var(--pink)" stroke-width="4"/>
      <circle role="img" aria-label="Chocolate sprinkled cone dessert" cx="965" cy="475" r="100" fill="#8e6048" stroke="var(--pink)" stroke-width="4"/>
      <circle role="img" aria-label="Shake glass with cherry" cx="1183" cy="296" r="50" fill="#b9554a" stroke="var(--pink)" stroke-width="4"/>
    </svg>
    <div class="brand"><span class="dot"></span>Treat Loft</div>
    <nav class="nav"><a>Menu</a><a>Locations</a><a>Catering</a><a>Shop</a><a>About us</a><a>Contact us</a></nav>
    <div class="menu-toggle" aria-label="Open menu"><span></span><span></span><span></span></div>
    <h1 class="hero-title heading">Fresh<br>And <span class="accent">Delicious</span></h1>
    <p class="hero-sub">Tradional food to delight the whole family</p>
    <a class="btn">Order Now</a>
  </header>

  <section class="about">
    <div class="about-frame"></div>
    <div class="photo" role="img" aria-label="Chef plating a dessert" style="left:104px;top:833px;width:494px;height:415px;background:linear-gradient(120deg,#3a2a22 0%,#c9b9ae 45%,#eee8e3 100%)"></div>
    <div class="about-bracket"></div>
    <h2 class="about-title heading">About <span class="accent">Us</span></h2>
    <p class="about-text">Lorem Ipsum is simply dummy text of the printing and typesetting industry. Lorem Ipsum has been the industry's standard dummy text ever since the 1500s,</p>
    <a class="btn">Read More</a>
  </section>

  <svg class="abs" style="left:0;top:1430px" width="1200" height="32" viewBox="0 0 1200 32">
    <path d="M0 20 L30 14 L55 18 L80 8 L110 16 L150 10 L190 18 L230 6 L270 15 L320 9 L360 17 L400 11 L450 19 L500 10 L540 16 L590 8 L640 18 L690 12 L730 20 L780 10 L830 17 L880 9 L930 19 L980 13 L1020 21 L1070 11 L1120 18 L1160 8 L1200 15 L1200 32 L0 32 Z" fill="var(--wine)"/>
  </svg>
  <div class="photo" role="img" aria-label="Popcorn bursting from a striped box" style="left:910px;top:1253px;width:250px;height:210px;background:radial-gradient(circle at 55% 45%,#e9c27a 0%,#d8a34f 45%,rgba(216,163,79,0) 72%)"></div>
  <section class="menu">
    <h2 class="menu-title heading">Menu</h2>
    <div class="tabs">
      <span style="left:32px">Soda/water</span>
      <span style="left:254px">PopCorns</span>
      <span class="active" style="left:496px">Ice Cream</span>
      <span style="left:749px">Shakes</span>
      <span style="left:975px">Soda/water</span>
    </div>
    <div class="photo" role="img" aria-label="Bowl of ice cream scoops with fruit" style="left:93px;top:376px;width:416px;height:225px;background:radial-gradient(ellipse at 50% 50%,#c8a6c2 0%,#9bae7c 35%,#efe6e1 60%,rgba(239,230,225,0) 72%)"></div>
    <div class="pill heading">Ice Cream</div>
    <p class="menu-text">Lorem Ipsum is simply dummy text of the printing and typesetting industry. Lorem Ipsum has been the industry's standard dummy text ever since the 1500s,</p>
    <div class="treat" style="left:539px"><div class="ring" role="img" aria-label="Sundae glass" style="background:#f6e7ea"></div>Lorem Ipsum</div>
    <div class="treat" style="left:659px"><div class="ring" role="img" aria-label="Chocolate scoops" style="background:#8b5a44"></div>Lorem Ipsum</div>
    <div class="treat" style="left:784px"><div class="ring" role="img" aria-label="Strawberry sundae" style="background:#e7a5b2"></div>Lorem Ipsum</div>
    <div class="treat" style="left:908px"><div class="ring" role="img" aria-label="Ice cream cone" style="background:var(--night)"></div>CLick For More</div>
    <div class="gift-cards">
      <div class="gift-card"><div class="thumb" role="img" aria-label="Popcorn gift bag" style="background:#e9c27a"></div><div><h3>Gift Bags</h3><p>Gourmet popcorn packed for parties and sleepovers.</p></div></div>
      <div class="gift-card"><div class="thumb" role="img" aria-label="Holiday popcorn tin" style="background:#c9a56b"></div><div><h3>Holiday Tins</h3><p>Festive tins filled with seasonal popcorn mixes.</p></div></div>
      <div class="gift-card"><div class="thumb" role="img" aria-label="Gift certificate" style="background:#f4c2cf"></div><div><h3>Gift Certificates</h3><p>A sweet treat for family, friends and teams.</p></div></div>
    </div>
  </section>

  <section class="gallery" role="img" aria-label="Ice cream display counter">
    <div class="gallery-title heading">Our <span class="accent">Galleries</span></div>
    <p class="gallery-text">Lorem Ipsum is simply dummy text of the printing and typesetting industry.<br>Lorem Ipsum has been the industry's standard dummy text ever since the 1500s<br>when an unknown printer took a galley of type and scrambled it to make a type<br>specimen book. It has survived not only five centuries</p>
    <a class="btn">View Gallery</a>
  </section>
  <svg class="abs" style="left:0;top:2262px" width="1200" height="40" viewBox="0 0 1200 40">
    <path d="M0 0 L1200 0 L1200 14 L1150 22 L1100 12 L1050 26 L1000 16 L950 30 L900 18 L850 24 L800 12 L750 22 L700 14 L650 28 L600 16 L550 24 L500 12 L450 26 L400 15 L350 23 L300 10 L250 24 L200 14 L150 28 L100 16 L50 24 L0 14 Z" fill="var(--pink-deep)"/>
  </svg>
  <svg class="abs" style="left:0;top:2930px" width="1200" height="40" viewBox="0 0 1200 40">
    <path d="M0 18 L45 10 L90 20 L140 8 L190 16 L240 6 L290 18 L340 10 L390 22 L440 12 L490 20 L540 8 L590 16 L640 10 L690 22 L740 12 L790 18 L840 6 L890 16 L940 10 L990 20 L1040 8 L1090 18 L1140 10 L1200 16 L1200 40 L0 40 Z" fill="var(--white)"/>
  </svg>
  <div class="photo" role="img" aria-label="Scoop of blueberry ice cream with berries" style="left:973px;top:2222px;width:187px;height:183px;background:radial-gradient(circle at 55% 42%,#a99ae0 0%,#8d7cd0 45%,rgba(141,124,208,0) 70%)"></div>
  <div class="video-slot" role="img" aria-label="Ad video area: milkshake with ice cream scoops and popcorn">
    <div class="play"><svg width="28" height="30" viewBox="0 0 28 30"><path d="M4 2 L26 15 L4 28 Z" fill="#fff"/></svg></div>
  </div>

  <section class="contact">
    <h2 class="contact-title heading">Contact Us</h2>
    <p class="contact-sub">When an unknown printer took a galley of type and scrambled it to</p>
    <div class="field" style="left:96px;top:3287px;width:340px;height:40px">Name</div>
    <div class="field" style="left:450px;top:3287px;width:341px;height:40px">Email Address</div>
    <div class="field" style="left:96px;top:3343px;width:695px;height:135px;padding-top:14px">Message</div>
    <div class="info">
      <h4 style="top:3282px">Telephone</h4>
      <p style="top:3313px;left:822px;letter-spacing:2px;font-style:italic">00-24680-1357</p>
      <h4 style="top:3346px">E-mail</h4>
      <p style="top:3378px">hello@treatloft.example</p>
      <h4 style="top:3411px">Address</h4>
      <p style="top:3444px;width:250px">When an unknown printer took a galley of type and scrambled it to</p>
    </div>
  </section>

  <svg class="abs" style="left:0;top:3620px" width="1200" height="32" viewBox="0 0 1200 32">
    <path d="M0 16 L40 8 L85 18 L130 6 L175 14 L220 10 L265 20 L310 8 L360 16 L410 10 L460 20 L510 8 L560 15 L610 6 L660 18 L710 10 L760 19 L810 8 L860 16 L910 10 L960 20 L1010 9 L1060 17 L1110 7 L1160 15 L1200 10 L1200 32 L0 32 Z" fill="var(--pink)"/>
  </svg>
  <footer class="footer">
    <div class="brand"><span class="dot"></span>Treat Loft</div>
    <p class="foot-about">Lorem Ipsum is simply dummy text of the printing and typesetting industry. Lorem Ipsum has been the industry's standard dummy text ever since the 1500s, when an unknown printer took a galley of type and scrambled it to make a type specimen book.</p>
    <div class="foot-col" style="left:501px"><h5>Quick Links</h5><ul><li>POPCORN</li><li>ICE CREAM</li><li>DRIZZLE</li><li>POP TARTS</li><li>MORE...</li></ul></div>
    <div class="foot-col" style="left:666px"><h5>Infromation</h5><ul><li>Online Enquiry</li><li>General Enquiries</li><li>Gift Bags</li><li>Privacy and Policy</li><li>Call Us</li></ul></div>
    <div class="foot-col" style="left:845px;width:300px"><h5>Have a Questions?</h5>
      <div class="contact-line"><svg width="14" height="14" viewBox="0 0 24 24"><path fill="#fff" d="M6.6 10.8a15 15 0 006.6 6.6l2.2-2.2c.3-.3.7-.4 1-.2 1.1.4 2.3.6 3.6.6.6 0 1 .4 1 1V20c0 .6-.4 1-1 1A17 17 0 013 4c0-.6.4-1 1-1h3.5c.6 0 1 .4 1 1 0 1.3.2 2.5.6 3.6.1.3 0 .7-.2 1z"/></svg>555-010-2040</div>
      <div class="contact-line"><svg width="16" height="12" viewBox="0 0 24 18"><rect width="24" height="18" rx="2" fill="#fff"/><path d="M2 2l10 8 10-8" fill="none" stroke="var(--pink)" stroke-width="2"/></svg>info@treatloft.example</div>
      <div class="contact-line"><svg width="14" height="18" viewBox="0 0 24 32"><path fill="#fff" d="M12 0A12 12 0 000 12c0 9 12 20 12 20s12-11 12-20A12 12 0 0012 0zm0 17a5 5 0 110-10 5 5 0 010 10z"/></svg>Dummy Address Lorem Ipsum Sit Amet<br>Dummy Pin Dummy place.</div>
    </div>
  </footer>
</div>
</body>
</html>
```